Pellowar

We need logo and wesbsite for a software development company based out of Hyderabad, India focused on startups and mid sized companies focused on build a new software products in USA and Europe countires.

Target Market(s)

startup and midsized companies in teh USA and Europe for software product development.

Industry/Entity Type

software development

Coding

Coded - Design and coding required

Number of Pages Required

5+ page

Requirements
Must have
• latest design concepts and very elegant
Nice to have
• each page should have images that reflects the content
Should not have
• too many colors

```html
<!DOCTYPE html>
<html lang="en">
<head>
<meta charset="utf-8">
<title>Pellowar – Build Your Product</title>
<link href="https://fonts.googleapis.com/css2?family=Open+Sans:wght@400;600;700&family=Noto+Sans:wght@300;400&display=swap" rel="stylesheet">
<style>
:root{
  --orange:#f0901e;
  --ink:#1f1f1f;
  --text:#333;
  --muted:#888;
  --band:#f8f6f7;
  --foot:#e9e9e9;
  --white:#fff;
}
*{box-sizing:border-box;margin:0;padding:0}
html,body{width:1200px;height:3005px;overflow:hidden;background:var(--white)}
body{font-family:"Open Sans",sans-serif;color:var(--text);position:relative}
.abs{position:absolute}
.brand{font-family:"Open Sans",sans-serif;font-weight:700;color:var(--ink);display:flex;align-items:center}
.brand-dot{border-radius:50%;background:var(--orange)}
.site-header .brand{left:98px;top:30px;font-size:34px;gap:12px}
.site-header .brand-dot{width:26px;height:26px}
.nav{left:581px;top:48px;font-size:13px;color:var(--ink)}
.nav a{position:absolute;white-space:nowrap;text-decoration:none;color:inherit}
.nav a.active{color:var(--orange)}
.nav a.active::after{content:"";position:absolute;left:0;right:0;top:39px;height:3px;background:var(--orange)}
.hero{left:0;top:93px;width:1200px;height:369px;background:linear-gradient(120deg,#e9e6ea 0%,#d9d4dc 30%,#c9d0e6 55%,#e8d9b0 75%,#d8c8cc 100%)}
.page-title{left:0;width:1200px;top:522px;text-align:center;font-family:"Noto Sans",sans-serif;font-weight:300;font-size:58px;color:var(--ink)}
.title-rule{left:533px;top:598px;width:134px;height:3px;background:var(--orange)}
.intro{left:220px;width:760px;top:650px;text-align:center;font-size:14px;line-height:23.5px}
.intro p{margin-bottom:23.5px}
.band{left:0;width:1200px;background:var(--band)}
.h2{font-family:"Noto Sans",sans-serif;font-weight:300;color:var(--ink)}
.team-head{left:148px;top:912px;font-size:23px;line-height:28px}
.team-list{left:188px;top:989px;list-style:none;font-size:14px;line-height:23.5px}
.team-list li{position:relative}
.team-list li::before{content:"";position:absolute;left:-19px;top:6px;width:11px;height:11px;border:1.5px solid var(--orange);border-radius:2px}
.team-list li::after{content:"";position:absolute;left:-16px;top:8px;width:4px;height:7px;border:solid var(--orange);border-width:0 2px 2px 0;transform:rotate(45deg)}
.team-art{left:571px;top:912px;width:404px;height:256px;border-radius:8px;background:linear-gradient(180deg,#fdf1e2 0%,#f5e8dc 60%,#ecdcd0 100%)}
.process-head{left:136px;top:1300px;font-size:24px;line-height:28.5px}
.process-list{left:627px;top:1290px;font-size:14px;line-height:23.5px;list-style:none;counter-reset:step}
.process-list li{counter-increment:step;position:relative;padding-left:26px}
.process-list li::before{content:counter(step) ".";position:absolute;left:0}
.iter-head{left:127px;top:1617px;font-size:24px;line-height:28.5px}
.iter-body{left:504px;width:606px;top:1624px;font-size:14px;line-height:19px}
.checks{list-style:none;margin-top:26px}
.checks li{position:relative;padding-left:30px;margin-bottom:14px;line-height:15px}
.checks li::before{content:"";position:absolute;left:8px;top:-2px;width:6px;height:12px;border:solid var(--orange);border-width:0 3px 3px 0;transform:rotate(40deg)}
.flow{left:499px;top:2047px;width:591px;height:338px;border:2px solid var(--orange);border-radius:14px;background:var(--white);padding:14px}
.flow-art{width:100%;height:100%;border-radius:8px;background:linear-gradient(135deg,#fff7ee 0%,#fde6cc 50%,#fff3e6 100%)}
.outro{left:504px;width:606px;top:2427px;font-size:14px;line-height:19px}
.outro p{margin-bottom:19px}
.site-footer .brand{left:93px;top:2790px;font-size:44px;gap:14px}
.site-footer .brand-dot{width:34px;height:34px}
.foot-head{font-family:"Noto Sans",sans-serif;font-weight:300;font-size:23px;color:var(--ink)}
.foot-head::after{content:"";display:block;width:48px;height:2px;background:var(--orange);margin-top:10px}
.links{left:443px;top:2685px}
.links ul{list-style:none;margin-top:14px;font-size:12px;line-height:23.5px}
.links li::before{content:"»";color:var(--orange);margin-right:7px}
.links li.active{color:var(--orange)}
.contact{left:752px;top:2685px}
.contact dl{margin-top:13px;font-size:14px}
.contact dt{font-weight:600;color:var(--ink);padding-left:20px;position:relative;margin-top:6px}
.contact dd{padding-left:20px;line-height:22px}
.contact dt svg{position:absolute;left:0;top:3px}
.copyright{left:0;top:2921px;width:1200px;height:84px;background:var(--foot);text-align:center;line-height:84px;font-size:11px;letter-spacing:4px;color:#666}
</style>
</head>
<body>
<header class="site-header">
  <div class="brand abs"><span class="brand-dot"></span>Pellowar</div>
  <nav class="nav abs">
    <a style="left:0">Home</a>
    <a style="left:57px">About Us</a>
    <a class="active" style="left:133px">Build Your Product</a>
    <a style="left:260px">Build Your Team</a>
    <a style="left:374px">Case Study</a>
    <a style="left:459px">Contact Us</a>
  </nav>
</header>

<div class="hero abs" role="img" aria-label="Photo of colourful game pawns connected by lines on a table"></div>

<h1 class="page-title abs">Build Your Product</h1>
<div class="title-rule abs"></div>
<div class="intro abs">
  <p>As startups are racing to build software as a product, they have stumbling blocks on building software from scratch. One of the reasons is stiff competition.</p>
  <p>The competition to get the best resources, robust design, and scalable technology is overwhelming.</p>
  <p>Startup owners must use the CEO mindset while building a software product. Think of the bigger picture. Focus on the outcome and set aside the tiny technical details. Focus on human resources and Process.</p>
</div>

<section class="band abs" style="top:855px;height:346px"></section>
<h2 class="team-head h2 abs">Software development needs experts.<br>Thus, your team will include:</h2>
<ul class="team-list abs">
  <li>Project Manager</li><li>Team Lead</li><li>Business analyst</li><li>Developers</li><li>Testers</li><li>Technical/Content Writers</li><li>UX Experts</li>
</ul>
<div class="team-art abs" role="img" aria-label="Illustration of a development team at a desk: front-end developer, back-end developer, QA and scrum master"></div>

<h2 class="process-head h2 abs">You need a step-by-step process to<br>achieve the result.<br>This is essential for combining<br>the people and technology to build the<br>product. Here are the processes:</h2>
<ol class="process-list abs">
  <li>Brainstorm for a product that will solve a problem</li>
  <li>Plan the entire process</li>
  <li>Incorporate ideas from business partners or stakeholders</li>
  <li>Design the product</li>
  <li>Outsource the development team</li>
  <li>Develop the product</li>
  <li>Deploy the product</li>
  <li>Sell the product to the target market</li>
</ol>

<section class="band abs" style="top:1547px;height:1074px"></section>
<h2 class="iter-head h2 abs">Building a product:<br>Split concept development<br>into iterations</h2>
<div class="iter-body abs">
  <p>It's worth remembering that each subsequent step of the product development process will be more expensive than the one before it. Pellowar proposes breaking down the development of a product into multiple iterations:</p>
  <ul class="checks">
    <li>Identify the issue and conduct interviews with possible users to validate the concept.</li>
    <li>Discuss the findings with the rest of the team, and do more research.</li>
    <li>Make prototypes to ensure that the initial concept appears as 'attractive' on paper as it does in your imagination.</li>
    <li>Examine the design and put it to the test with representatives of your target audience.</li>
    <li>Review customer comments and feedback and make changes/amendments to the design/concept as a whole.</li>
    <li>Make iterations on the prototypes and collect feedback, then assess and make modifications based on the input (if necessary).</li>
    <li>Create a Minimum Viable Product (MVP) and show it to potential clients (early adopters).</li>
    <li>Repeat the iteration process until the MVP satisfies high market demand or is deemed a failure.</li>
  </ul>
</div>

<div class="flow abs">
  <div class="flow-art" role="img" aria-label="Roadmap illustration of ten iteration steps, from spotting the problem to analysing feedback and improving the MVP"></div>
</div>

<div class="outro abs">
  <p>This approach gives more flexibility, allowing for the full-scale product concept review without spending your budget on something nobody will use.</p>
  <p>In totality, the whole process goes smoothly to help you reach your goals. With expert Pellowar teams, you are in the right hands and towards your goals. Pellowar helps you take care of all business affairs and takes care of activities along the way. Uncover a whole new range of innovative ideas to take a step closer to your goals.</p>
</div>

<footer class="site-footer">
  <div class="brand abs"><span class="brand-dot"></span>Pellowar</div>
  <div class="links abs">
    <h3 class="foot-head">Main Links</h3>
    <ul>
      <li>Home</li><li>About Us</li><li class="active">Build Your Product</li><li>Build Your Team</li><li>Case Study</li><li>Contact Us</li>
    </ul>
  </div>
  <div class="contact abs">
    <h3 class="foot-head">Contact Us</h3>
    <dl>
      <dt><svg width="12" height="14" viewBox="0 0 12 14"><path d="M6 0a5 5 0 0 0-5 5c0 4 5 9 5 9s5-5 5-9a5 5 0 0 0-5-5zm0 7a2 2 0 1 1 0-4 2 2 0 0 1 0 4z" fill="#f0901e"/></svg>Address:</dt>
      <dd>48 Harlow Street, Dallas, TX 75201</dd>
      <dt><svg width="13" height="13" viewBox="0 0 13 13"><path d="M3 1l2 3-1.5 1.5a8 8 0 0 0 4 4L9 8l3 2-1 2C6 12 1 7 1 2z" fill="none" stroke="#f0901e" stroke-width="1.4"/></svg>Phone:</dt>
      <dd>1-800-555-01-22</dd>
      <dt><svg width="15" height="11" viewBox="0 0 15 11"><rect x="0.5" y="0.5" width="14" height="10" fill="#f0901e"/><path d="M1 1l6.5 5L14 1" fill="none" stroke="#fff" stroke-width="1.2"/></svg>Mail:</dt>
      <dd>hello@pellowar.dev</dd>
    </dl>
  </div>
  <div class="copyright abs">COPYRIGHT © 2022 PELLOWAR</div>
</footer>
</body>
</html>
```